We (R. T. Galvin & Partners, Inc.) are an executive Search firm based in Los Angeles that is exclusively focused in the Med Tech and Health Tech arenas.   I need a logo to communicate that we are a high end search firm, but also that we are focused in the medicine and science arenas called health tech and med tech.  Many of our clients have robotics and artificial intelligence type products, so it is very technology forward.  I tend to gravitate towards clean, sharp aesthetic as opposed to something that is really over the top.
Attached are files with my logo in two different layouts.  In addition to the letterhead and envelope, I also will need an electronic letterhead in Microsoft Word.  I tend to
I look forward to seeing the designs and just let me know if you have any questions.
Dale

```html
<!DOCTYPE html>
<html lang="en">
<head>
<meta charset="utf-8">
<title>R. T. Galvin &amp; Partners, Inc. — Stationery</title>
<link href="https://fonts.googleapis.com/css2?family=Montserrat:wght@300;400&family=Poppins:wght@600&family=Roboto:wght@400&display=swap" rel="stylesheet">
<style>
  :root {
    --backdrop: #7a7a7a;
    --paper: #f7f7f7;
    --ink: #1a1a1a;
    --text: #4a4a4a;
    --muted: #5c5c5c;
    --brand-blue: #52a3dc;
    --band-black: #050505;
    --signature-tint: #dfe8f2;
  }
  * { margin: 0; padding: 0; box-sizing: border-box; }
  html, body { width: 1200px; height: 877px; overflow: hidden; background: var(--backdrop); }
  .canvas { position: relative; width: 1200px; height: 877px; }

  .sheet { position: absolute; background: var(--paper); overflow: hidden; }

  .brand-name {
    font-family: "Poppins", sans-serif; font-weight: 600; color: var(--ink);
    line-height: 1.15; display: flex; align-items: center; gap: 8px;
  }
  .brand-name .dot { width: 10px; height: 10px; border-radius: 50%; background: var(--brand-blue); flex: none; }
  .brand-name .lines span { display: block; }

  .footer-band { position: absolute; left: 0; bottom: 0; width: 100%; height: 9px; }

  /* Letterhead */
  .letterhead { left: 69px; top: 64px; width: 527px; height: 742px; }
  .letterhead .brand-name { position: absolute; left: 39px; top: 67px; font-size: 14px; }
  .letterhead .brand-name .lines span + span { font-size: 9px; letter-spacing: 1.2px; }
  .contact { position: absolute; top: 68px; font-family: "Roboto", sans-serif; font-size: 8px; color: var(--muted); line-height: 10.4px; }
  .contact-address { right: 157px; text-align: right; }
  .contact-divider { position: absolute; left: 378px; top: 67px; width: 1px; height: 33px; background: var(--brand-blue); }
  .contact-lines { left: 388px; }
  .contact-lines div { display: flex; align-items: center; gap: 4px; }
  .contact-lines svg { width: 7px; height: 7px; flex: none; }

  .letter { position: absolute; left: 46px; top: 206px; width: 440px; font-family: "Montserrat", sans-serif; font-weight: 300; color: var(--text); }
  .salutation { font-size: 13.5px; margin-bottom: 22px; font-weight: 400; color: #444; }
  .letter p { font-size: 7.4px; line-height: 11.4px; margin-bottom: 11.6px; text-align: justify; }
  .closing { margin-top: 21px; }
  .signature { position: absolute; left: 41px; top: 518px; width: 94px; height: 38px; background: var(--signature-tint); border-radius: 3px; }

  /* Envelope back */
  .envelope-back { left: 614px; top: 269px; width: 530px; height: 240px; }
  .envelope-back .flap { position: absolute; left: 0; top: 0; }
  .flap-dot { position: absolute; left: 257px; top: 29px; width: 16px; height: 16px; border-radius: 50%; background: #fff; }

  /* Envelope front */
  .envelope-front { left: 614px; top: 562px; width: 533px; height: 242px; }
  .envelope-front .brand-name { position: absolute; left: 26px; top: 34px; font-size: 14px; }
  .envelope-front .brand-name .lines span + span { font-size: 8.5px; letter-spacing: 1.1px; }
  .return-address { position: absolute; left: 72px; top: 72px; font-family: "Roboto", sans-serif; font-size: 7.6px; line-height: 10px; color: var(--muted); }
</style>
</head>
<body>
<div class="canvas">

  <section class="sheet letterhead">
    <div class="brand-name">
      <span class="dot"></span>
      <div class="lines"><span>R. T. GALVIN</span><span>&amp; PARTNERS INC.</span></div>
    </div>

    <div class="contact contact-address">
      2140 Larkfield Avenue<br>
      Los Angeles, California 90017<br>
      www.rtgalvinpartners.com
    </div>
    <div class="contact-divider"></div>
    <div class="contact contact-lines">
      <div><svg viewBox="0 0 10 10"><path d="M2 1l2 2-1 1.3c.6 1.2 1.5 2.1 2.7 2.7L7 6l2 2-1.2 1.5C4.5 9.2.8 5.5.5 2.2z" fill="#52a3dc"/></svg>310-555-0142</div>
      <div><svg viewBox="0 0 10 10"><rect x="2.5" y="0.5" width="5" height="9" rx="1" fill="none" stroke="#52a3dc"/></svg>310-555-0187</div>
      <div><svg viewBox="0 0 10 10"><rect x="0.5" y="2" width="9" height="6" fill="#52a3dc"/><path d="M0.5 2l4.5 3.5L9.5 2" fill="none" stroke="#fff" stroke-width=".8"/></svg>info@rtgalvinpartners.com</div>
    </div>

    <div class="letter">
      <div class="salutation">Dear Mr. Harlow,</div>
      <p>Lorem ipsum dolor sit amet, consectetur adipiscing elit. Donec orci purus, luctus vitae dignissim eu, iaculis sed purus. Vivamus faucibus, ipsum nec aliquet viverra, leo mauris condimentum ligula, sit amet sagittis enim ligula quis arcu. Nam egestas tortor id nisi porttitor mattis. In tortor ante, ultricies in suscipit a, tempus non massa. Vivamus et auctor mi. Fusce vel massa nulla. Phasellus nec eros mauris, et scelerisque orci.</p>
      <p>Donec malesuada orci vitae nulla accumsan porta a id massa. Quisque accumsan iaculis magna sit amet fringilla. Maecenas consequat, magna eget tincidunt semper, odio nibh rutrum mi, id feugiat ante nisi eu risus. Vestibulum nunc orci, rhoncus a placerat in, ultricies in mi. Cras mattis varius eros, vel fringilla nisi suscipit eget. Quisque scelerisque sagittis nulla at porttitor.</p>
      <p>Sed id augue vitae urna euismod commodo aliquet a quam. Pellentesque arcu velit, cursus et malesuada ut, consequat et diam. Nullam erat sem, rhoncus id ullamcorper vitae, rhoncus et arcu. In ultricies ultricies nulla, ut rutrum nisi iaculis at. Donec eu magna a metus ornare faucibus. Fusce aliquet faucibus ultricies. Morbi semper, est id tincidunt gravida, sem arcu adipiscing lacus, ac bibendum nulla leo eu purus. Quisque nec diam sed risus consectetur a ccumsan quis quis nibh. Vestibulum id purus lorem.</p>
      <p>It is a long established fact that a reader will be distracted by the readable content of a page when looking at its layout. The point of using Lorem Ipsum is that it has a more-or-less normal distribution of letters, as opposed to using 'Content here, content here', making it look like readable English. Many desktop publishing packages</p>
      <p class="closing">Sincerely,</p>
    </div>
    <div class="signature" role="img" aria-label="Handwritten signature of Paul Reyes"></div>

    <svg class="footer-band" viewBox="0 0 527 9" preserveAspectRatio="none">
      <rect width="527" height="9" fill="#050505"/>
      <polygon points="0,0 339,0 346,9 0,9" fill="#52a3dc"/>
    </svg>
  </section>

  <section class="sheet envelope-back">
    <svg class="flap" width="530" height="76" viewBox="0 0 530 76">
      <path d="M0 0H530L522 40Q516 74 482 74H48Q14 74 8 40Z" fill="#52a3dc"/>
    </svg>
    <span class="flap-dot"></span>
  </section>

  <section class="sheet envelope-front">
    <div class="brand-name">
      <span class="dot"></span>
      <div class="lines"><span>R. T. GALVIN</span><span>&amp; PARTNERS INC.</span></div>
    </div>
    <div class="return-address">
      2140 Larkfield Avenue<br>
      Los Angeles, California 90017
    </div>
    <svg class="footer-band" viewBox="0 0 533 9" preserveAspectRatio="none">
      <rect width="533" height="9" fill="#050505"/>
      <polygon points="0,0 345,0 352,9 0,9" fill="#52a3dc"/>
    </svg>
  </section>

</div>
</body>
</html>
```